Marlowe Group needs a business card

I would like the card to be simple but modern and elegant.
I like black and white.
or black and gold.
we are a private finance lender and also are involved in property and property developments.

please look at the business card photos i provided i would like M.G only one one side and all the other details on the other side use fonts that tie in with my theme.

Industry/Entity Type

Finance

Contact Information for Business Card

Marlowe Group (M.G) Daniel Marlowe M: 0413586207 E: danmarl@inboxmail.test

Font styles to use
Other font styles liked:
• Use fonts that would reflect our business

Colors
000000
ffffff

Requirements
Must have
• one side of details
• other side has either M.G or Marlowe Group like in the photos provided

```html
<!DOCTYPE html>
<html lang="en">
<head>
<meta charset="UTF-8">
<title>Marlowe Group — Business Card</title>
<link href="https://fonts.googleapis.com/css2?family=Montserrat:wght@400;600&display=swap" rel="stylesheet">
<style>
  :root {
    --backdrop: #1b1b1d;
    --card-black: #232324;
    --gold: #d9bf7a;
    --gold-soft: #c9ae6a;
  }
  * { margin: 0; padding: 0; box-sizing: border-box; }
  html, body {
    width: 1200px;
    height: 786px;
    overflow: hidden;
    background: var(--backdrop);
  }
  .canvas {
    width: 1200px;
    height: 786px;
    display: flex;
    align-items: center;
    justify-content: center;
    gap: 60px;
  }
  .card {
    width: 510px;
    height: 292px;
    background: var(--card-black);
    display: flex;
    flex-direction: column;
    align-items: center;
    justify-content: center;
    box-shadow: 0 10px 30px rgba(0, 0, 0, 0.45);
  }
  .card-details { gap: 22px; }
  .holder-name {
    font-family: "Montserrat", sans-serif;
    font-weight: 600;
    font-size: 17px;
    letter-spacing: 0.08em;
    text-transform: uppercase;
    color: var(--gold);
  }
  .contact-line {
    font-family: "Montserrat", sans-serif;
    font-weight: 400;
    font-size: 12.5px;
    letter-spacing: 0.06em;
    color: var(--gold-soft);
  }
  .contact-line .divider { margin: 0 6px; }
  .company-name {
    font-family: "Montserrat", sans-serif;
    font-weight: 400;
    font-size: 34px;
    letter-spacing: 0.22em;
    text-transform: uppercase;
    color: var(--gold);
    line-height: 1;
    padding-left: 0.22em;
  }
</style>
</head>
<body>
  <main class="canvas">
    <section class="card card-details" aria-label="Card back with contact details">
      <h1 class="holder-name">Daniel Marlowe</h1>
      <p class="contact-line">M: 0413586207<span class="divider">|</span>E: danmarl@inboxmail.test</p>
    </section>
    <section class="card card-front" aria-label="Card front with company name">
      <p class="company-name">Marlowe Group</p>
    </section>
  </main>
</body>
</html>
```